Lumavento business card

We need a modern business card - With our 4 colors - See web: www.lumavento.dk

I have attached logo and som old business Cards we have - Lets Make the new ones shine...:-) -

Industry/Entity Type

Business

Requirements
Must have
• the logo with lumavento only,

```html
<!DOCTYPE html>
<html lang="da">
<head>
<meta charset="utf-8">
<title>Lumavento – visitkort</title>
<link rel="stylesheet" href="https://fonts.googleapis.com/css2?family=Source+Sans+3:wght@400;600&display=swap">
<style>
  :root {
    --lime: #a6c93a;
    --plum: #6b1f6e;
    --magenta: #e0138c;
    --ink: #3d3d3d;
    --paper: #ffffff;
    --backdrop: #ecebe8;
  }
  * { margin: 0; padding: 0; box-sizing: border-box; }
  html, body { width: 1200px; height: 900px; overflow: hidden; }
  body {
    background: var(--backdrop);
    font-family: "Source Sans 3", sans-serif;
    position: relative;
  }
  .card {
    position: absolute;
    border-radius: 18px;
    overflow: hidden;
    box-shadow: 0 6px 18px rgba(0,0,0,0.12);
  }
  .card-front { left: 78px; top: 34px; width: 588px; height: 364px; background: var(--paper); }
  .card-back  { left: 389px; top: 506px; width: 565px; height: 350px; background: var(--lime); }

  .band { position: absolute; left: 0; right: 0; }
  .card-front .band { top: 29px; height: 99px; background: var(--lime); }
  .card-back .band  { top: 81px; height: 96px; background: var(--paper); }

  .badge { position: absolute; border-radius: 50%; }
  .card-front .badge { width: 152px; height: 152px; left: 219px; top: 5px; background: var(--paper); }
  .card-back .badge  { width: 164px; height: 164px; left: 209px; top: 47px; background: var(--lime); }

  .wordmark {
    position: absolute; left: 0; right: 0; text-align: center;
    font-weight: 400; letter-spacing: 3px;
  }
  .card-front .wordmark { top: 126px; font-size: 19px; color: var(--ink); }
  .card-back .wordmark  { top: 195px; font-size: 21px; color: var(--paper); }

  .rule { position: absolute; height: 3px; }
  .card-front .rule { left: 187px; width: 212px; top: 160px; background: var(--lime); }
  .card-back .rule  { left: 161px; width: 254px; top: 233px; background: var(--paper); }

  .tagline { position: absolute; left: 0; right: 0; text-align: center; }
  .card-front .tagline { top: 172px; font-size: 14px; color: var(--ink); }
  .card-back .tagline  { top: 248px; font-size: 16px; color: var(--paper); }

  .person { position: absolute; left: 39px; top: 220px; }
  .person-name { font-size: 22px; font-weight: 600; color: var(--plum); line-height: 1.1; }
  .person-title { font-size: 15px; color: var(--magenta); margin-top: 4px; }
  .address { position: absolute; left: 39px; top: 282px; font-size: 16px; line-height: 23px; color: var(--magenta); }

  .contact { position: absolute; right: 36px; top: 246px; list-style: none; }
  .contact li {
    display: flex; justify-content: flex-end; align-items: center; gap: 12px;
    font-size: 16px; line-height: 25px; color: var(--magenta);
  }
  .contact svg { width: 12px; height: 12px; fill: var(--plum); }
</style>
</head>
<body>

<section class="card card-front" aria-label="Visitkort forside">
  <div class="band"></div>
  <div class="badge"></div>
  <div class="wordmark">lumavento</div>
  <div class="rule"></div>
  <div class="tagline">Medier til unge</div>

  <div class="person">
    <div class="person-name">Marius Holmgaard</div>
    <div class="person-title">Salgsdirektør</div>
  </div>
  <div class="address">Kastanievej 14 - 8000<br>Aarhus -Tlf. 86 12 47 30</div>

  <ul class="contact">
    <li>+45 61 42 73 18
      <svg viewBox="0 0 24 24" aria-hidden="true"><path d="M6.6 10.8a15 15 0 0 0 6.6 6.6l2.2-2.2a1 1 0 0 1 1-.25 11.4 11.4 0 0 0 3.6.57 1 1 0 0 1 1 1V20a1 1 0 0 1-1 1A17 17 0 0 1 3 4a1 1 0 0 1 1-1h3.5a1 1 0 0 1 1 1c0 1.25.2 2.45.57 3.6a1 1 0 0 1-.25 1z"/></svg>
    </li>
    <li>mh@lumavento.dk
      <svg viewBox="0 0 24 24" aria-hidden="true"><path d="M2 5h20v14H2z M3 6l9 7 9-7" stroke="#fff" stroke-width="1.5"/></svg>
    </li>
    <li>www.lumavento.dk
      <svg viewBox="0 0 24 24" aria-hidden="true"><circle cx="12" cy="12" r="11"/><path d="M1 12h22M12 1c3 3.5 3 18.5 0 22M12 1c-3 3.5-3 18.5 0 22" stroke="#fff" stroke-width="1.4" fill="none"/></svg>
    </li>
  </ul>
</section>

<section class="card card-back" aria-label="Visitkort bagside">
  <div class="band"></div>
  <div class="badge"></div>
  <div class="wordmark">lumavento</div>
  <div class="rule"></div>
  <div class="tagline">Medier til unge</div>
</section>

</body>
</html>
```